Need business card with a logo for a hearing aid sales and audiology business. We have two Hearing Instrument Specialists and one Audiologist on staff. Over 25 years in business. Locally owned and operated. Financing available. Most insurances accepted.

Summit Audio Wellness LLC
48730 W Larchmont, Suite 7
Spokane, WA 99281
509-617-2084
www.summitaudiowell.example

Manager
Tobias Kerrell HIS COHC
License #71829046

Target Market(s)

50yr old + people with a hearing loss.

Industry/Entity Type

Business

Contact Information for Business Card

48730 W Larchmont, Suite 7
Spokane, WA 99281
509-617-2084
www.summitaudiowell.example

Manager
Tobias Kerrell HIS COHC
NLVE #71829046

Font styles to use
Serif
Sans Serif

Requirements
Must have
• Business name, Tobias's name and title(s) and contact information, License #, web address

```html
<!DOCTYPE html>
<html lang="en">
<head>
<meta charset="utf-8">
<title>Summit Audio Wellness LLC – Business Card</title>
<link rel="stylesheet" href="https://fonts.googleapis.com/css2?family=Open+Sans:wght@400;600;700&display=swap">
<style>
  :root {
    --backdrop: #3b3e43;
    --brand-green: #1f6108;
    --brand-blue: #1a64a6;
    --ink: #222426;
    --ink-soft: #3c3f42;
    --card-white: #f7f7f7;
    --rule: #9a9a9a;
  }
  * { margin: 0; padding: 0; box-sizing: border-box; }
  html, body {
    width: 1200px; height: 864px; overflow: hidden;
    background: var(--backdrop);
    font-family: "Open Sans", Arial, sans-serif;
  }
  .stage {
    width: 1200px; height: 864px;
    display: flex; flex-direction: column; align-items: center; justify-content: center;
    gap: 44px;
  }
  .card {
    width: 560px; height: 320px; position: relative;
    box-shadow: 0 6px 18px rgba(0,0,0,.35);
  }

  /* Front */
  .card-front {
    background: var(--brand-green);
    display: flex; flex-direction: column; align-items: center; justify-content: center;
    gap: 16px;
  }
  .front-mark {
    width: 26px; height: 26px; border-radius: 50%;
    background: #ffffff;
  }
  .front-name {
    color: #ffffff; font-weight: 600; font-size: 25px; letter-spacing: .2px;
  }

  /* Back */
  .card-back { background: var(--card-white); }
  .brand-block {
    position: absolute; right: 34px; top: 44px;
    display: flex; flex-direction: column; align-items: center;
  }
  .brand-mark {
    width: 22px; height: 22px; background: var(--brand-blue); margin-bottom: 10px;
  }
  .brand-name {
    color: var(--brand-blue); font-weight: 600; font-size: 21px;
    padding-bottom: 6px; border-bottom: 1px solid var(--rule);
  }
  .person {
    position: absolute; left: 40px; top: 134px;
  }
  .person-name { color: var(--brand-blue); font-weight: 700; font-size: 16px; }
  .person-creds { color: var(--brand-blue); font-weight: 400; font-size: 14px; }
  .person-title { color: var(--ink-soft); font-size: 13px; line-height: 1.2; }
  .license {
    position: absolute; right: 34px; top: 208px;
    font-weight: 700; font-size: 14px; color: var(--brand-green);
  }
  .license-number { color: var(--ink); }
  .contact {
    position: absolute; right: 34px; top: 236px;
    list-style: none; text-align: right;
    font-size: 13.5px; color: var(--ink); line-height: 1.5;
  }
  .contact li { display: flex; align-items: center; justify-content: flex-end; gap: 6px; }
  .contact svg { width: 12px; height: 12px; flex: none; }
  .contact .no-icon { padding-right: 18px; }
</style>
</head>
<body>
  <main class="stage">
    <section class="card card-front" aria-label="Card front">
      <span class="front-mark"></span>
      <p class="front-name">Summit Audio Wellness LLC</p>
    </section>

    <section class="card card-back" aria-label="Card back">
      <div class="brand-block">
        <span class="brand-mark"></span>
        <p class="brand-name">Summit Audio Wellness LLC</p>
      </div>

      <div class="person">
        <p><span class="person-name">Tobias Kerrell</span> <span class="person-creds">HIS COHC</span></p>
        <p class="person-title">Manager</p>
      </div>

      <p class="license">License <span class="license-number">#71829046</span></p>

      <ul class="contact">
        <li>509-617-2084
          <svg viewBox="0 0 24 24" aria-hidden="true"><path fill="#1a64a6" d="M6.6 10.8a15.1 15.1 0 0 0 6.6 6.6l2.2-2.2a1 1 0 0 1 1-.25 11.4 11.4 0 0 0 3.6.57 1 1 0 0 1 1 1V20a1 1 0 0 1-1 1A17 17 0 0 1 3 4a1 1 0 0 1 1-1h3.5a1 1 0 0 1 1 1c0 1.25.2 2.45.57 3.57a1 1 0 0 1-.25 1z"/></svg>
        </li>
        <li>www.summitaudiowell.example
          <svg viewBox="0 0 24 24" aria-hidden="true"><circle cx="12" cy="12" r="10" fill="#1a64a6"/><path d="M2 12h20M12 2c3 3 3 17 0 20M12 2c-3 3-3 17 0 20" stroke="#fff" stroke-width="1.4" fill="none"/></svg>
        </li>
        <li class="no-icon">48730 W Larchmont, Suite 7 Spokane, WA 99281</li>
      </ul>
    </section>
  </main>
</body>
</html>
```